Home Security Company Business Card

Looking for a eye catching business card that is non traditional and stands out but yet still looks professional. It should include all the pertinent information such as name, title, address, telephone, e-mail, website address should definitely stand out and then finally the logo.

Target Market(s)

Residential and Commercial accounts mostly upscale accounts

Industry/Entity Type

Security

Contact Information for Business Card

Name
Title
Address
Office #
Cell #
E-mail
Website

Font styles to use
Serif
Sans Serif

Requirements
Must have
• Logo, two sided color configuration
Nice to have
• You decide
Should not have
• There really aren't any.

```html
<!DOCTYPE html>
<html lang="en">
<head>
<meta charset="utf-8">
<title>Bastion Home Protection – Business Card</title>
<link href="https://fonts.googleapis.com/css2?family=Lato:wght@400;700;900&display=swap" rel="stylesheet">
<style>
  :root {
    --maroon: #7d1208;
    --maroon-deep: #5e0c05;
    --gold: #d9a21e;
    --paper: #f7f6f4;
    --ink: #1e1e1e;
    --stage: #2a2a2a;
    --back-text: #ead9d6;
  }
  * { box-sizing: border-box; margin: 0; padding: 0; }
  html, body { width: 1200px; height: 997px; overflow: hidden; }
  body {
    background: var(--stage);
    font-family: "Lato", sans-serif;
    display: flex;
    flex-direction: column;
    align-items: center;
    justify-content: center;
    gap: 40px;
  }
  .card {
    width: 770px;
    height: 440px;
    position: relative;
    overflow: hidden;
    box-shadow: 0 12px 30px rgba(0,0,0,.5);
  }

  /* Back side */
  .card-back {
    background: radial-gradient(ellipse at 35% 40%, #8e1608 0%, var(--maroon) 55%, var(--maroon-deep) 100%);
  }
  .card-back .brand {
    position: absolute;
    right: 54px;
    bottom: 56px;
    display: flex;
    align-items: center;
    gap: 14px;
    color: var(--back-text);
    font-weight: 700;
    font-size: 30px;
    letter-spacing: .5px;
  }
  .brand-dot {
    width: 22px; height: 22px; border-radius: 50%;
    background: currentColor;
  }

  /* Front side */
  .card-front { background: var(--paper); }
  .band-top {
    position: absolute; left: 0; right: 0; top: 0;
    height: 16px; background: var(--maroon);
    border-bottom: 4px solid var(--gold);
  }
  .band-bottom {
    position: absolute; left: 0; right: 0; bottom: 0;
    height: 74px; background: var(--maroon);
    border-top: 4px solid var(--gold);
    display: flex; align-items: center; justify-content: center;
  }
  .website {
    color: #fff; font-size: 19px; letter-spacing: 7px; font-weight: 400;
  }
  .front-brand {
    position: absolute; left: 50px; top: 190px;
    display: flex; align-items: center; gap: 12px;
    color: var(--maroon); font-weight: 700; font-size: 25px;
  }
  .identity {
    position: absolute; left: 420px; top: 60px;
  }
  .person-name {
    color: var(--maroon); font-weight: 900; font-size: 21px; letter-spacing: .3px;
  }
  .person-title { color: var(--ink); font-size: 16px; margin-top: 2px; }
  .contacts {
    position: absolute; left: 420px; top: 170px;
    list-style: none; display: flex; flex-direction: column; gap: 8px;
  }
  .contacts li {
    display: flex; align-items: center; gap: 14px;
    font-size: 16px; color: var(--ink);
  }
  .icon-box {
    width: 32px; height: 32px; background: var(--maroon);
    display: flex; align-items: center; justify-content: center;
  }
  .icon-box svg { width: 18px; height: 18px; fill: #fff; }
</style>
</head>
<body>

  <section class="card card-back" aria-label="Card back">
    <div class="brand"><span class="brand-dot"></span>Bastion Home Protection Inc.</div>
  </section>

  <section class="card card-front" aria-label="Card front">
    <div class="band-top"></div>

    <div class="front-brand"><span class="brand-dot"></span>Bastion Home<br>Protection Inc.</div>

    <div class="identity">
      <p class="person-name">DANIEL MERCER</p>
      <p class="person-title">Owner / Founder</p>
    </div>

    <ul class="contacts">
      <li>
        <span class="icon-box"><svg viewBox="0 0 24 24"><path d="M4 9c0-3 4-5 8-5s8 2 8 5v2h-4V9c-1-1-7-1-8 0v2H4z"/><path d="M6 13h12l2 7H4z"/></svg></span>
        1.305.555.0142
      </li>
      <li>
        <span class="icon-box"><svg viewBox="0 0 24 24"><path d="M7 2h10a1 1 0 0 1 1 1v18a1 1 0 0 1-1 1H7a1 1 0 0 1-1-1V3a1 1 0 0 1 1-1zm1 3v13h8V5z"/></svg></span>
        1.305.555.0187
      </li>
      <li>
        <span class="icon-box"><svg viewBox="0 0 24 24"><path d="M2 5h20v14H2zm2 2v.5l8 5.5 8-5.5V7zm0 3v7h16v-7l-8 5.5z"/></svg></span>
        daniel@bastionhome.com
      </li>
      <li>
        <span class="icon-box"><svg viewBox="0 0 24 24"><path d="M12 2a7 7 0 0 1 7 7c0 5-7 13-7 13S5 14 5 9a7 7 0 0 1 7-7zm0 4a3 3 0 1 0 0 6 3 3 0 0 0 0-6z"/></svg></span>
        24 Harbor Lane, Kota Damai, Malaysia
      </li>
    </ul>

    <div class="band-bottom"><span class="website">www.bastionhomeprotection.com</span></div>
  </section>

</body>
</html>
```